Need Business Card for our Real Estate Business with Sales Executive's Picture

PANTONE 484 C ( RED)

PANTONE 2766 C ( BLUE

Industry/Entity Type

Real Estate

Contact Information for Business Card

Name, Mobile, email, & picture of Person
Agency Phone, address, Web address

Requirements
Must have
• Our Logo Colours, Agent Picture,

```html
<!DOCTYPE html>
<html lang="en">
<head>
<meta charset="utf-8">
<title>Meridian Homes – Business Card</title>
<link rel="stylesheet" href="https://fonts.googleapis.com/css2?family=Amaranth:wght@700&family=Open+Sans:wght@400;600&display=swap">
<style>
  :root {
    --page-bg: #e9e6e2;
    --card-navy-dark: #17285a;
    --card-navy: #213a78;
    --card-navy-light: #2b4891;
    --brand-red: #a8322d;
    --text-light: #ece8ee;
    --text-soft: #d9d6e0;
    --logo-cream: #f1e6d6;
    --photo-warm: #b98a72;
    --photo-shirt: #d9d4d6;
    --photo-suit: #2a4382;
    --photo-suit-dark: #1a2c5e;
  }
  * { margin: 0; padding: 0; box-sizing: border-box; }
  html, body { width: 1200px; height: 1054px; overflow: hidden; }
  body {
    background: var(--page-bg);
    font-family: "Open Sans", Arial, sans-serif;
    position: relative;
  }
  .business-card {
    position: absolute;
    left: 100px; top: 224px;
    width: 1000px; height: 606px;
    border-radius: 6px;
    overflow: hidden;
    background: radial-gradient(ellipse at 45% 40%, var(--card-navy-light) 0%, var(--card-navy) 45%, var(--card-navy-dark) 100%);
    box-shadow: 0 18px 40px rgba(0,0,0,0.25);
  }
  .agent-photo {
    position: absolute;
    z-index: 0;
    left: 545px; top: 38px;
    width: 455px; height: 568px;
    border-radius: 190px 190px 0 0;
    background:
      radial-gradient(ellipse 26% 22% at 52% 24%, var(--photo-warm) 0%, var(--photo-warm) 70%, rgba(185,138,114,0) 100%),
      radial-gradient(ellipse 14% 40% at 44% 72%, var(--photo-shirt) 0%, rgba(217,212,214,0.6) 60%, rgba(217,212,214,0) 100%),
      linear-gradient(180deg, var(--photo-suit) 0%, var(--photo-suit) 55%, var(--photo-suit-dark) 100%);
  }
  .brand {
    position: absolute;
    z-index: 1;
    left: 52px; top: 86px;
    display: flex; align-items: center; gap: 16px;
  }
  .brand-square {
    width: 26px; height: 26px;
    background: var(--logo-cream);
  }
  .brand-name {
    font-weight: 600;
    font-size: 38px;
    letter-spacing: 3px;
    color: var(--logo-cream);
    line-height: 1;
    white-space: nowrap;
  }
  .agent {
    position: absolute;
    z-index: 1;
    left: 52px; top: 262px;
  }
  .agent-name {
    font-family: "Amaranth", "Trebuchet MS", sans-serif;
    font-weight: 700;
    font-size: 37px;
    color: var(--text-light);
    line-height: 1.1;
  }
  .agent-title {
    font-size: 24px;
    color: var(--text-soft);
    margin-top: 4px;
  }
  .contact-list {
    position: absolute;
    z-index: 1;
    left: 52px; top: 360px;
    list-style: none;
  }
  .contact-list li {
    display: flex; align-items: flex-start;
    font-size: 24px;
    line-height: 35px;
    color: var(--text-light);
  }
  .contact-list svg {
    width: 22px; height: 22px;
    margin: 7px 22px 0 0;
    flex: none;
    fill: var(--brand-red);
  }
</style>
</head>
<body>
  <div class="business-card">
    <div class="agent-photo" role="img" aria-label="Portrait photo of the sales executive in a navy suit and striped tie"></div>

    <div class="brand">
      <span class="brand-square"></span>
      <span class="brand-name">MERIDIAN HOMES</span>
    </div>

    <div class="agent">
      <div class="agent-name">Dana Whitfield</div>
      <div class="agent-title">Managing Director</div>
    </div>

    <ul class="contact-list">
      <li>
        <svg viewBox="0 0 24 24" aria-hidden="true"><rect x="6" y="1" width="12" height="22" rx="2"/><rect x="8" y="4" width="8" height="13" fill="var(--card-navy)"/></svg>
        555.201.4478
      </li>
      <li>
        <svg viewBox="0 0 24 24" aria-hidden="true"><path d="M2 8c0-3 4-5 10-5s10 2 10 5v2h-5V8H7v2H2z"/><path d="M5 12h14l2 9H3z"/></svg>
        555-309-6612
      </li>
      <li>
        <svg viewBox="0 0 24 24" aria-hidden="true"><path d="M2 5h20v14H2z"/><path d="M2 5l10 8 10-8" fill="none" stroke="var(--card-navy)" stroke-width="2"/></svg>
        dwhitfield@meridianhomesco.com
      </li>
      <li>
        <svg viewBox="0 0 24 24" aria-hidden="true"><circle cx="12" cy="12" r="10"/><path d="M2 12h20M12 2c4 4 4 16 0 20M12 2c-4 4-4 16 0 20" fill="none" stroke="var(--card-navy)" stroke-width="1.5"/></svg>
        www.meridianhomesco.com
      </li>
      <li>
        <svg viewBox="0 0 24 24" aria-hidden="true"><path d="M12 1a8 8 0 0 0-8 8c0 6 8 14 8 14s8-8 8-14a8 8 0 0 0-8-8z"/><circle cx="12" cy="9" r="3" fill="var(--card-navy)"/></svg>
        <span>48 Alder Ridge Rd #210,<br>Fairview, CO 80000</span>
      </li>
    </ul>
  </div>
</body>
</html>
```